Packaging and labelling for Swiss made Organic CBD Oil

Visit our website www.clearleafmerida.example
We have not put any product on yet as require packaging and label design .
Website will give you a great feel for the company and how we have used
the logo . The Vextora cbd product shown is a company similar to ourselves with similar core values , we liked the clean packaging design they have .

Im happy if you want use the mandala symbol in our logo separate from
KELVORA, to separate and use the mandala symbol as a larger icon than
it appears in our logo
Clean , Pure , organic feel. Like the product to look pharmaceutical and life changing not gimmicky.
Colours to go with or be the same as our logo colours
But not too cold and clinical
Bottle size 84mm x 25mm
Label size 75mm x 30mm
Box 30mm x 30mm x 100mm
6 products
Full Spectrum :
500mg CBD (5%)
1000mg CBD ( 10% )
1500mg CBD (15%)
2000mg CBD ( 20% )
Broad spectrum THC Free
500mg CBD (5%)
Pets
500mg Broad Spectrum THC Free
Updates

Would like the design to be more modern than traditional

LABEL Information Front of Bottle - Logo KELVORA & Mandala - Mandala can be used separately as design symbol Organic Cannabis Oil 1500mg CBD (15%) Ful Spectrum 10ml Back of bottle Ingredients: Organic Cannabis Oil Extract Organic Sunflower Seed Oil THC - 0.2% Certified Swiss Organic Cultivation Shake well before use. Store in a cool , dry place and out of the each of children BOX information Front and rear Logo - KELVORA & Mandala - Mandala can be used separately as a design symbol Organic Cannabis Oil 1500mg CBD (15%) Full Spectrum Sides x 2 This product is a food supplement and is not intended to diagnose, treat, cure or prevent any disease If you are pregnant, lactating or taking any medication consult your health care practitioner Suitable for vegetarians and vegans Ingredients Organic Cannabis Oil extract Organis Sunflower Oil Store in a cool ,dry place, out of the reach of children Recommended Use 1-5 drops ( 1 drop = 7.5mg CBD ) Subject to body weight and personal requirement - visit www.clearleafmerida for more information 100% Natural 100% Organic GMO free 100% Vegan ( symbol with each ) Expiry date see bottle label Cultivated and manufactured in Switzerland

Target Market(s)

age 40 - 80

Font styles to use
Other font styles liked:
• In our website we have used Open Sans for the copy and Lato for headings .

Requirements
Must have
• look like an Industry leader
Kelvora will change the quality of peoples lives and in some cases may
even save lives so want look powerful and credible
Our Mission is - Through Delivering Pure , Premium , Organic products we will educate, inform and help people achieve healthier , happier lifestyles
Nice to have
• Colours to look good with our logo colours or be the same as our logo
colours
Logo Font - Avenir Black and Avenir Book

Font used in website - Content - Open Sans / Headings - Lato
If you have another font for the packaging information that will go well with
our logo, I'm happy for you to use your skills

```html
<!DOCTYPE html>
<html lang="en">
<head>
<meta charset="utf-8">
<title>Kelvora Organic Cannabis Oil – Label and Box Sides</title>
<link href="https://fonts.googleapis.com/css2?family=Nunito+Sans:wght@800&family=Open+Sans:wght@300;400;600&display=swap" rel="stylesheet">
<style>
  :root {
    --teal: #8fd3d1;
    --teal-text: #7fcfcc;
    --teal-faint: #e9f6f6;
    --grey-logo: #8c8c8c;
    --grey-text: #9b9b9b;
    --grey-dark: #777777;
    --frame: #a8a8a8;
    --guide: #55e3ec;
    --green: #7ab648;
    --red: #e2212b;
    --swiss-grey: #8a8a8a;
    --ink: #111111;
    --paper: #ffffff;
  }
  html, body { margin: 0; padding: 0; overflow: hidden; background: var(--paper); }
  .artboard { display: block; width: 1200px; height: 1000px; }
  .frame { fill: none; stroke: var(--frame); stroke-width: 1; }
  .guide { stroke: var(--guide); stroke-width: 1; }
  .section-title { font-family: "Open Sans", sans-serif; font-size: 17px; fill: var(--ink); }
  .brand { font-family: "Nunito Sans", sans-serif; font-weight: 800; fill: var(--grey-logo); letter-spacing: 0.5px; }
  .brand-dot { fill: none; stroke: var(--teal); stroke-width: 1.2; }
  .badge-organic { fill: var(--green); }
  .badge-swiss { fill: var(--red); }
  .badge-made { fill: var(--swiss-grey); }
  .product { font-family: "Open Sans", sans-serif; font-weight: 300; fill: var(--grey-dark); }
  .strength { font-family: "Open Sans", sans-serif; font-weight: 300; fill: var(--grey-dark); }
  .copy { font-family: "Open Sans", sans-serif; font-weight: 300; fill: var(--grey-text); }
  .copy-key { fill: var(--teal-text); font-weight: 400; }
  .copy-strong { font-weight: 600; fill: var(--grey-dark); }
  .icon-ring { fill: none; stroke: var(--teal); stroke-width: 2; }
  .icon-glyph { fill: var(--teal); }
  .icon-line { fill: none; stroke: var(--teal); stroke-width: 2.2; stroke-linecap: round; stroke-linejoin: round; }
  .icon-label { font-family: "Open Sans", sans-serif; font-weight: 600; font-size: 9.5px; fill: var(--teal-text); text-anchor: middle; }
</style>
</head>
<body>
<svg class="artboard" viewBox="0 0 1200 1000" xmlns="http://www.w3.org/2000/svg">
  <defs>
    <radialGradient id="mandala-soft" cx="50%" cy="50%" r="50%">
      <stop offset="0%" stop-color="#bfe6e5"/>
      <stop offset="70%" stop-color="#e4f4f4"/>
      <stop offset="100%" stop-color="#ffffff"/>
    </radialGradient>
    <radialGradient id="mandala-faint" cx="50%" cy="50%" r="50%">
      <stop offset="0%" stop-color="#f1f9f9"/>
      <stop offset="100%" stop-color="#ffffff" stop-opacity="0"/>
    </radialGradient>
  </defs>

  <!-- Section titles -->
  <text class="section-title" x="265" y="441" text-anchor="middle">Label for bottle V1</text>
  <text class="section-title" x="265" y="703" text-anchor="middle">Label for bottle V2</text>
  <text class="section-title" x="672" y="381" text-anchor="middle">Box sides</text>

  <!-- Bottle label V1 -->
  <g class="bottle-label" transform="translate(44,457)">
    <rect class="frame" x="0" y="0" width="411" height="164"/>
    <text class="copy" font-size="12" transform="translate(16,86) rotate(-90)" text-anchor="middle">10 ml</text>
    <circle class="brand-dot" cx="45" cy="18" r="5"/>
    <text class="brand" x="51" y="30" font-size="19">KELVORA</text>
    <g class="seal">
      <rect class="badge-organic" x="52" y="67" width="66" height="14"/>
      <rect class="badge-swiss" x="120" y="67" width="13" height="14"/>
      <rect class="badge-made" x="135" y="68" width="16" height="12"/>
    </g>
    <text class="product" x="51" y="98" font-size="18">Cannabis Oil</text>
    <text class="strength" x="51" y="130" font-size="11.5">1500 mg CBD (15%)</text>
    <text class="product" x="51" y="148" font-size="17">Full Spectrum</text>
    <text class="copy" font-size="10" transform="translate(202,152) rotate(-90)">
      <tspan x="0" y="0">Ingredients: Organic Cannabis</tspan>
      <tspan x="0" dy="12.5">Oil Extract, Organic Sunflower Oil</tspan>
    </text>
    <text class="copy" font-size="10" transform="translate(235,152) rotate(-90)">
      <tspan x="0" y="0">Certified swiss organic</tspan>
      <tspan x="0" dy="12.5">cultivation and 100% natural</tspan>
    </text>
    <text class="copy" font-size="12" transform="translate(270,152) rotate(-90)">THC below 0.2%</text>
    <text class="copy" font-size="10" transform="translate(293,152) rotate(-90)">
      <tspan x="0" y="0">Shake well before use. Store</tspan>
      <tspan x="0" dy="12.5">in a cool, dry place, out of the</tspan>
      <tspan x="0" dy="12.5">reach of children.</tspan>
    </text>
    <text class="copy" font-size="10" transform="translate(336,152) rotate(-90)">
      <tspan x="0" y="0" class="copy-key">Recommended Use:</tspan>
      <tspan x="0" dy="11.6">1-5 drops. Subject to body</tspan>
      <tspan x="0" dy="11.6">weight and personal</tspan>
      <tspan x="0" dy="11.6">requirement – visit</tspan>
      <tspan x="0" dy="11.6">www.clearleafmerida.example</tspan>
      <tspan x="0" dy="11.6">for more information.</tspan>
    </text>
  </g>

  <!-- Bottle label V2 -->
  <g class="bottle-label" transform="translate(44,720)">
    <rect x="20" y="2" width="190" height="160" fill="url(#mandala-faint)" role="img" aria-label="Faint mandala symbol behind the front panel"/>
    <rect class="frame" x="0" y="0" width="411" height="164"/>
    <text class="copy" font-size="12" transform="translate(16,86) rotate(-90)" text-anchor="middle">10 ml</text>
    <circle class="brand-dot" cx="45" cy="18" r="5"/>
    <text class="brand" x="51" y="30" font-size="19">KELVORA</text>
    <g class="seal">
      <rect class="badge-organic" x="52" y="67" width="66" height="14"/>
      <rect class="badge-swiss" x="120" y="67" width="13" height="14"/>
      <rect class="badge-made" x="135" y="68" width="16" height="12"/>
    </g>
    <text class="product" x="51" y="98" font-size="18">Cannabis Oil</text>
    <text class="strength" x="51" y="130" font-size="11.5">1500 mg CBD (15%)</text>
    <text class="product" x="51" y="148" font-size="17">Full Spectrum</text>
    <text class="copy" font-size="10" transform="translate(202,152) rotate(-90)">
      <tspan x="0" y="0">Ingredients: Organic Cannabis</tspan>
      <tspan x="0" dy="12.5">Oil Extract, Organic Sunflower Oil</tspan>
    </text>
    <text class="copy" font-size="10" transform="translate(235,152) rotate(-90)">
      <tspan x="0" y="0">Certified swiss organic</tspan>
      <tspan x="0" dy="12.5">cultivation and 100% natural</tspan>
    </text>
    <text class="copy" font-size="12" transform="translate(270,152) rotate(-90)">THC below 0.2%</text>
    <text class="copy" font-size="10" transform="translate(293,152) rotate(-90)">
      <tspan x="0" y="0">Shake well before use. Store</tspan>
      <tspan x="0" dy="12.5">in a cool, dry place, out of the</tspan>
      <tspan x="0" dy="12.5">reach of children.</tspan>
    </text>
    <text class="copy" font-size="10" transform="translate(336,152) rotate(-90)">
      <tspan x="0" y="0" class="copy-key">Recommended Use:</tspan>
      <tspan x="0" dy="11.6">1-5 drops. Subject to body</tspan>
      <tspan x="0" dy="11.6">weight and personal</tspan>
      <tspan x="0" dy="11.6">requirement – visit</tspan>
      <tspan x="0" dy="11.6">www.clearleafmerida.example</tspan>
      <tspan x="0" dy="11.6">for more information.</tspan>
    </text>
  </g>

  <!-- Box top panel -->
  <g class="box-top" transform="translate(827,53)">
    <rect class="frame" x="0" y="0" width="329" height="328"/>
    <rect x="80" y="95" width="160" height="135" rx="67" fill="url(#mandala-soft)" role="img" aria-label="Large teal mandala symbol"/>
  </g>

  <!-- Box sides -->
  <g class="box-sides" transform="translate(499,399)">
    <rect x="10" y="70" width="460" height="420" fill="url(#mandala-faint)" role="img" aria-label="Faint oversized mandala symbol across the box side"/>
    <rect x="520" y="200" width="137" height="200" fill="url(#mandala-faint)" role="img" aria-label="Faint mandala petals at the panel edge"/>
    <rect class="frame" x="0" y="0" width="657" height="547"/>
    <line class="frame" x1="328" y1="0" x2="328" y2="547"/>

    <!-- Side panel A -->
    <g class="side-front">
      <circle class="brand-dot" cx="19" cy="40" r="6"/>
      <text class="brand" x="26" y="54" font-size="22">KELVORA</text>
      <g class="seal">
        <rect class="badge-organic" x="18" y="268" width="87" height="18"/>
        <rect class="badge-swiss" x="107" y="268" width="17" height="18"/>
        <rect class="badge-made" x="126" y="269" width="21" height="16"/>
      </g>
      <text class="product" x="17" y="311" font-size="25">Cannabis Oil</text>
      <text class="strength" x="17" y="465" font-size="15.5">1500 mg CBD (15%)</text>
      <text class="product" x="17" y="491" font-size="21.5">Full Spectrum</text>
      <text class="strength" x="18" y="532" font-size="14.5">Made in Switzerland</text>

      <text class="copy" font-size="10.8">
        <tspan x="176" y="206">This product is a food</tspan>
        <tspan x="176" dy="11.6">supplement and is not</tspan>
        <tspan x="176" dy="11.6">intended to diagnose, treat,</tspan>
        <tspan x="176" dy="11.6">cure or prevent any disease.</tspan>
        <tspan x="177" y="261">If you are pregnant, lactating</tspan>
        <tspan x="177" dy="11.6">or taking any medication</tspan>
        <tspan x="177" dy="11.6">consult your health care</tspan>
        <tspan x="177" dy="11.6">practitioner.</tspan>
        <tspan x="176" y="316">Suitable for vegetarians</tspan>
        <tspan x="176" dy="11.6">and vegans.</tspan>
        <tspan x="176" y="348"><tspan class="copy-strong">Ingredients:</tspan> Organic Cannabis</tspan>
        <tspan x="176" dy="11.6">Oil Extract, Organic Sunflower Oil</tspan>
        <tspan x="176" y="380">Store in a cool, dry place, out</tspan>
        <tspan x="176" dy="11.6">of the reach of children.</tspan>
        <tspan x="176" y="412" class="copy-key" font-size="11.5">Batch No and Lab Results</tspan>
        <tspan x="176" y="425">Visit <tspan class="copy-strong" font-size="8.6">www.kelvoraorganic.example/</tspan></tspan>
        <tspan x="176" dy="11.6"><tspan class="copy-strong" font-size="8.6">labresults</tspan> for independent</tspan>
        <tspan x="176" dy="11.6">third party lab test results for</tspan>
        <tspan x="176" dy="11.6">this product</tspan>
        <tspan x="176" y="480">Batch No and expiry date see</tspan>
        <tspan x="176" dy="11.6">label on bottom of box</tspan>
      </text>
      <text class="strength" x="246" y="527" font-size="14" text-anchor="middle">10 ml</text>
    </g>

    <!-- Side panel B -->
    <g class="side-back" transform="translate(328,0)">
      <circle class="brand-dot" cx="19" cy="40" r="6"/>
      <text class="brand" x="26" y="54" font-size="22">KELVORA</text>
      <g class="seal">
        <rect class="badge-organic" x="18" y="268" width="87" height="18"/>
        <rect class="badge-swiss" x="107" y="268" width="17" height="18"/>
        <rect class="badge-made" x="126" y="269" width="21" height="16"/>
      </g>
      <text class="product" x="17" y="311" font-size="25">Cannabis Oil</text>
      <text class="strength" x="18" y="465" font-size="15.5">1500 mg CBD (15%)</text>
      <text class="product" x="18" y="491" font-size="21.5">Full Spectrum</text>
      <text class="strength" x="19" y="532" font-size="14.5">Made in Switzerland</text>

      <text class="copy" font-size="10.8">
        <tspan x="175" y="34" class="copy-key">Recommended Use:</tspan>
        <tspan x="175" dy="12.8">Shake well before use. 1-5</tspan>
        <tspan x="175" dy="12.8">drops (1 drop = 7.5mg CBD)</tspan>
        <tspan x="175" dy="12.8">Subject to body weight and</tspan>
        <tspan x="175" dy="12.8">personal requirement – visit</tspan>
        <tspan x="175" dy="12.8">www.clearleafmerida.example</tspan>
        <tspan x="175" dy="12.8">for more information.</tspan>
      </text>

      <g class="claim">
        <circle class="icon-ring" cx="245" cy="167" r="25"/>
        <path class="icon-glyph" d="M245 150 C256 158 256 172 245 182 C234 172 234 158 245 150 Z"/>
        <line class="icon-line" x1="245" y1="160" x2="245" y2="188" stroke="#ffffff" stroke-width="1.4"/>
        <text class="icon-label" x="245" y="203">100% Natural</text>
      </g>
      <g class="claim">
        <circle class="icon-ring" cx="245" cy="249" r="25"/>
        <path class="icon-glyph" d="M241 234 C247 240 247 247 241 251 C235 247 235 240 241 234 Z"/>
        <path class="icon-line" d="M231 257 C238 254 243 258 249 258 L258 254 M231 263 L246 264 L259 256"/>
        <text class="icon-label" x="245" y="285">100% Organic</text>
      </g>
      <g class="claim">
        <circle class="icon-ring" cx="245" cy="332" r="25"/>
        <path class="icon-line" d="M235 318 L235 346 M231 318 L231 326 Q235 330 239 326 L239 318"/>
        <path class="icon-glyph" d="M244 318 C249 320 249 330 244 332 Z"/>
        <line class="icon-line" x1="244" y1="318" x2="244" y2="346"/>
        <path class="icon-glyph" d="M253 320 C259 324 259 332 253 336 C247 332 247 324 253 320 Z"/>
        <line class="icon-line" x1="253" y1="334" x2="253" y2="346"/>
        <text class="icon-label" x="245" y="369">100% Vegan</text>
      </g>
      <g class="claim">
        <circle class="icon-ring" cx="245" cy="415" r="25"/>
        <path class="icon-line" d="M241 401 L249 401 M243 401 L243 411 L235 428 L255 428 L247 411 L247 401"/>
        <path class="icon-glyph" d="M239 420 L251 420 L255 428 L235 428 Z"/>
        <text class="icon-label" x="245" y="453">GMO Free</text>
      </g>

      <text class="strength" x="244" y="507" font-size="16.5" text-anchor="middle">THC below 0.2%</text>
      <text class="strength" x="244" y="527" font-size="14" text-anchor="middle">10 ml</text>
    </g>
  </g>

  <!-- Fold guides -->
  <line class="guide" x1="63" y1="40" x2="63" y2="957"/>
  <line class="guide" x1="227" y1="40" x2="227" y2="957"/>
  <line class="guide" x1="663" y1="40" x2="663" y2="957"/>
  <line class="guide" x1="990" y1="40" x2="990" y2="957"/>
</svg>
</body>
</html>
```